Asphalt Driveway Billboard Design

We need a billboard designed for an Asphalt & Concrete Company in Minnesota. We want to advertise Asphalt Driveways on this billboard! Logo is uploaded below. Our website is pinecrest-paving.com for more information.

```html
<!DOCTYPE html>
<html lang="en">
<head>
<meta charset="utf-8">
<title>Pinecrest Asphalt &amp; Concrete — Driveway Billboard</title>
<link rel="stylesheet" href="https://fonts.googleapis.com/css2?family=Montserrat:wght@600;700;800&family=Oswald:wght@600&display=swap">
<style>
  :root {
    --page-bg: #e9ecef;
    --ink-dark: #231f20;
    --brand-blue: #1a8bc9;
    --ribbon-blue: #0d5ea8;
    --deep-blue: #0b4f94;
    --sky-light: #dff1fd;
    --accent-cyan: #4cc3f0;
    --tape-yellow: #f5d50a;
    --white: #ffffff;
    --photo-asphalt: #4a4d52;
    --photo-house: #8c8f8a;
    --photo-sky: #9cc8e8;
  }
  html, body {
    margin: 0;
    width: 1200px;
    height: 1200px;
    overflow: hidden;
    background: var(--page-bg);
  }
  .billboard {
    position: absolute;
    left: 0;
    top: 425px;
    width: 1200px;
    height: 350px;
    display: block;
    box-shadow: 0 10px 30px rgba(0,0,0,0.18);
  }
  .brand-name { font-family: "Montserrat", sans-serif; font-weight: 800; fill: var(--ink-dark); }
  .brand-tagline { font-family: "Montserrat", sans-serif; font-weight: 700; fill: var(--ink-dark); letter-spacing: 2px; }
  .web-address { font-family: "Montserrat", sans-serif; font-weight: 700; fill: var(--white); }
  .phone-number { font-family: "Montserrat", sans-serif; font-weight: 800; fill: var(--white); }
  .estimate-note { font-family: "Montserrat", sans-serif; font-weight: 600; fill: var(--accent-cyan); }
  .headline { font-family: "Oswald", sans-serif; font-weight: 600; fill: var(--white); }
</style>
</head>
<body>
<svg class="billboard" viewBox="0 0 1200 350" xmlns="http://www.w3.org/2000/svg">
  <defs>
    <linearGradient id="info-panel-fill" x1="0" y1="0" x2="0.3" y2="1">
      <stop offset="0" stop-color="var(--sky-light)"/>
      <stop offset="1" stop-color="var(--white)"/>
    </linearGradient>
    <linearGradient id="photo-left-fill" x1="0" y1="0" x2="0" y2="1">
      <stop offset="0" stop-color="var(--photo-house)"/>
      <stop offset="0.45" stop-color="#6f7370"/>
      <stop offset="1" stop-color="var(--photo-asphalt)"/>
    </linearGradient>
    <linearGradient id="photo-right-fill" x1="0" y1="0" x2="0" y2="1">
      <stop offset="0" stop-color="var(--photo-sky)"/>
      <stop offset="0.35" stop-color="#b9ab98"/>
      <stop offset="0.7" stop-color="#2f3238"/>
      <stop offset="1" stop-color="#55585c"/>
    </linearGradient>
  </defs>

  <!-- info panel background -->
  <rect class="info-panel" x="0" y="0" width="1200" height="350" fill="url(#info-panel-fill)"/>

  <!-- photography area -->
  <g class="photo-area">
    <rect x="0" y="0" width="260" height="350" fill="url(#photo-left-fill)" role="img" aria-label="Photo of a grey two-storey house with a freshly paved asphalt driveway"/>
    <path d="M250 0 H660 Q600 170 560 350 H200 Z" fill="url(#photo-right-fill)" role="img" aria-label="Photo of a large suburban house with a three-car garage and a newly sealed black asphalt driveway"/>
    <path d="M250 0 L200 350" stroke="var(--white)" stroke-width="5"/>
  </g>

  <!-- curved blue divider -->
  <path class="divider-curve" d="M660 0 Q600 170 560 350 H600 Q640 170 700 0 Z" fill="var(--white)"/>
  <path class="divider-curve" d="M680 0 Q622 170 585 350 H610 Q650 170 712 0 Z" fill="var(--brand-blue)"/>

  <!-- dark contact band -->
  <path class="contact-band" d="M604 350 Q614 300 630 245 H1200 V350 Z" fill="var(--ink-dark)"/>

  <!-- brand block -->
  <g class="brand-block">
    <text class="brand-name" x="935" y="150" font-size="74" text-anchor="middle">PINECREST</text>
    <line x1="735" y1="186" x2="770" y2="186" stroke="var(--ink-dark)" stroke-width="3"/>
    <text class="brand-tagline" x="935" y="194" font-size="22" text-anchor="middle">ASPHALT &amp; CONCRETE</text>
    <line x1="1100" y1="186" x2="1135" y2="186" stroke="var(--ink-dark)" stroke-width="3"/>
  </g>

  <!-- website pill -->
  <rect class="web-pill" x="690" y="212" width="480" height="48" rx="24" fill="var(--brand-blue)"/>
  <text class="web-address" x="930" y="246" font-size="32" text-anchor="middle">www.pinecrest-paving.com</text>

  <!-- phone line -->
  <text class="estimate-note" x="705" y="306" font-size="18" text-anchor="end">FREE</text>
  <text class="estimate-note" x="705" y="326" font-size="18" text-anchor="end">ESTIMATE</text>
  <text class="phone-number" x="715" y="330" font-size="70" textLength="465" lengthAdjust="spacingAndGlyphs">763-555-0148</text>

  <!-- headline ribbon -->
  <path class="headline-ribbon" d="M0 300 L545 268 L515 333 L0 350 Z" fill="var(--ribbon-blue)"/>
  <path class="headline-accent" d="M0 344 L513 336 L510 342 L0 350 Z" fill="var(--tape-yellow)"/>
  <text class="headline" x="22" y="334" font-size="46" transform="rotate(-3.2 22 334)" textLength="480" lengthAdjust="spacingAndGlyphs">ASPHALT DRIVEWAY SPECIALISTS</text>
</svg>
</body>
</html>
```